A private security company called "Tavron Security Services Ltd"

Hello everybody,

We need a web page for a company based in NZ. It is mainly an informative website so it would be wonderful if the designer puts their absolute best into making it a website that I would really appreciate. The website needs to show professionalism and also needs to make our web surfers find the information they need in a click. the company's colour is black and silver, and if those two colours could be integrated into the website it would be absolutely lovely. Please do contact me for any information.

Sincerely,
Dorian Vaskel

Industry/Entity Type

Security

```html
<!DOCTYPE html>
<html lang="en">
<head>
<meta charset="utf-8">
<title>Tavron Security Services Ltd</title>
<link rel="stylesheet" href="https://fonts.googleapis.com/css2?family=Open+Sans:ital,wght@0,300;0,400;0,600;0,700;1,400&family=Raleway:wght@300;400&family=Lora:ital@1&display=swap">
<style>
:root{
  --black:#0b0b0b;
  --ink:#1c1c1c;
  --text:#555;
  --muted:#8a8a8a;
  --silver:#c9cbcd;
  --light:#f1f1f1;
  --white:#fff;
  --footer:#2b2b2b;
  --footer-line:#444;
  --footer-text:#9a9a9a;
}
*{margin:0;padding:0;box-sizing:border-box}
html,body{width:1200px;height:2514px;overflow:hidden}
body{position:relative;font-family:"Open Sans",Arial,sans-serif;color:var(--text);background:var(--white)}

/* header */
.site-header{position:absolute;left:0;top:0;width:1200px;height:111px;background:var(--black);z-index:3}
.brand{position:absolute;left:114px;top:30px;display:flex;align-items:center;gap:10px;color:var(--white)}
.brand-mark{width:14px;height:14px;background:var(--silver)}
.brand-name{font-size:17px;font-weight:700;letter-spacing:1px;line-height:1.2}
.main-nav a{position:absolute;top:0;height:111px;line-height:114px;font-size:14px;font-weight:600;color:var(--white);text-decoration:none}
.main-nav a.active{background:var(--white);color:var(--ink);width:79px;text-align:center}

/* hero */
.hero{position:absolute;left:0;top:111px;width:1200px;height:533px;z-index:1}
.hero-photo{position:absolute;inset:0;background:linear-gradient(115deg,#e9ebee 0%,#cfd3d7 45%,#b9bdc1 70%,#8c5a4a 100%)}
.hero-caption{position:absolute;left:109px;top:110px;width:411px;height:235px;background:rgba(255,255,255,.93);padding:26px 16px}
.hero-caption h1{font-size:25px;font-weight:700;color:var(--ink);line-height:1.2}
.hero-caption h2{font-size:22px;font-weight:400;color:#333;line-height:1.3}
.hero-caption p{font-size:12.5px;color:var(--muted);line-height:1.45;margin-top:14px}
.btn-dark{display:inline-block;background:var(--ink);color:var(--white);font-size:13.5px;padding:0 14px;height:35px;line-height:35px;border-radius:2px}
.hero-caption .btn-dark{margin-top:18px}

/* welcome */
.welcome{position:absolute;left:0;top:644px;width:1200px;height:362px;background:var(--light);z-index:1}
.welcome h2{position:absolute;left:113px;top:206px;font-size:28px;font-weight:300;color:#333}
.welcome h2 strong{font-weight:600}
.welcome p{position:absolute;left:113px;top:252px;width:870px;font-size:12.5px;line-height:1.5;color:var(--muted)}

/* services, above hero and welcome */
.service{position:absolute;top:580px;width:318px;height:208px;background:var(--black);color:var(--white);text-align:center;z-index:2}
.service-icon{position:absolute;left:92px;top:-67px;width:134px;height:134px;border-radius:50%;background:var(--white);border:5px solid var(--black);outline:3px solid var(--white);display:flex;align-items:center;justify-content:center}
.service h3{margin-top:86px;font-size:19px;font-weight:600}
.service p{font-size:12.5px;line-height:1.5;color:#ddd;padding:10px 16px 0}

/* security plus */
.plus{position:absolute;left:0;top:1006px;width:1200px;height:419px;background:var(--white)}
.plus-dot{position:absolute;left:111px;top:54px;width:44px;height:44px;border-radius:50%;background:var(--ink)}
.plus h2{position:absolute;left:208px;top:52px;font-family:"Raleway",sans-serif;font-weight:400;font-size:34px;color:#222;letter-spacing:.5px}
.plus .lead{position:absolute;left:208px;top:100px;width:270px;font-size:14px;line-height:1.35;color:#b0b0b0}
.checklist{position:absolute;left:111px;top:168px;list-style:none}
.checklist li{display:flex;align-items:center;gap:10px;height:30px;font-size:14px;color:#333}
.plus .btn-dark{position:absolute;left:111px;top:303px;height:38px;line-height:38px;font-size:12.5px;font-weight:600;padding:0 16px}
.plus-monitor{position:absolute;left:690px;top:62px;width:361px;height:298px;border-radius:8px;background:linear-gradient(180deg,#2a2a2a 0%,#555 62%,#d6d8da 70%,#eef0f1 100%)}

/* why */
.why{position:absolute;left:0;top:1425px;width:1200px;height:415px;background:var(--light)}
.why h2{position:absolute;left:110px;top:28px;font-size:23px;font-weight:700;color:var(--ink)}
.why .lead{position:absolute;left:110px;top:60px;font-size:14.5px;color:#444}
.reason{position:absolute;top:114px;width:311px}
.reason-photo{height:166px}
.reason h3{margin-top:20px;font-size:15.5px;font-weight:700;color:var(--ink)}
.reason p{margin-top:8px;font-size:12.5px;line-height:1.55;color:var(--muted)}

/* testimonials */
.testimonials{position:absolute;left:0;top:1840px;width:1200px;height:389px;background:var(--white)}
.testimonials h2{position:absolute;left:110px;top:40px;font-size:30px;font-weight:600;color:var(--ink)}
.testimonials .lead{position:absolute;left:110px;top:80px;font-size:13px;color:var(--muted)}
.avatar{position:absolute;top:154px;width:92px;height:92px;border-radius:50%;background:linear-gradient(135deg,#d8d8d8,#9a9a9a)}
.quote-card{position:absolute;top:154px;width:342px;height:193px;background:var(--white);box-shadow:2px 3px 6px rgba(0,0,0,.14);padding:30px 22px 0 44px;font-family:"Lora",serif;font-style:italic}
.quote-card::before{content:"";position:absolute;left:-12px;top:36px;border:12px solid transparent;border-left:0;border-right-color:var(--white)}
.quote-card .mark{position:absolute;font-size:54px;color:#ddd;line-height:1;font-style:normal;font-family:Georgia,serif}
.quote-card .open{left:14px;top:6px}
.quote-card .close{right:26px;bottom:8px}
.quote-card p{font-size:13px;line-height:1.5;color:#aaa}
.quote-card cite{display:block;margin-top:14px;font-size:15px;color:#333}

/* footer */
.site-footer{position:absolute;left:0;top:2229px;width:1200px;height:285px;background:var(--footer);color:var(--footer-text)}
.footer-col{position:absolute;top:44px}
.footer-col h4{font-size:20px;font-weight:600;color:var(--white);margin-bottom:14px}
.footer-col ul{list-style:none}
.footer-col li{font-size:12px;height:22px;line-height:22px}
.footer-col li::before{content:"▸ ";font-size:9px}
.footer-col li.active{color:var(--white)}
.contact-col p{font-size:12.5px;line-height:1.55;margin-bottom:10px;width:210px}
.social{display:flex;gap:5px;margin-top:6px}
.social span{width:24px;height:24px;border-radius:50%;background:#555}
.footer-rule{position:absolute;left:111px;top:240px;width:978px;height:1px;background:var(--footer-line)}
.copyright{position:absolute;left:0;top:252px;width:1200px;text-align:center;font-size:12.5px;color:var(--white)}
</style>
</head>
<body>

<header class="site-header">
  <div class="brand"><span class="brand-mark"></span><span class="brand-name">TAVRON<br>Security Services Ltd</span></div>
  <nav class="main-nav">
    <a class="active" href="#" style="left:541px">HOME</a>
    <a href="#" style="left:635px">ABOUT US</a>
    <a href="#" style="left:732px">SECURITY SERVICES</a>
    <a href="#" style="left:888px">TESTIMONIALS</a>
    <a href="#" style="left:1014px">CONTCT US</a>
  </nav>
</header>

<section class="hero">
  <div class="hero-photo" role="img" aria-label="Photo of a white surveillance camera mounted under a house eave"></div>
  <div class="hero-caption">
    <h1>YOUR LOGICAL</h1>
    <h2>choice for security services</h2>
    <p>Lorem ipsum dolor amet consectetur elit sed do eiusmod tempor incididunt ut labore et dolore magna aliqua.Ut enim ad minim veniam, quis nostrud exercitation ullamco laboris.</p>
    <span class="btn-dark">Read More</span>
  </div>
</section>

<section class="welcome">
  <h2>Welcome to <strong>Tavron Security Services LTD.</strong></h2>
  <p>Lorem ipsum dolor amet consectetur elit sed do eiusmod tempor incididunt ut labore et dolore magna aliqua.Ut enim ad minim veniam, quis nostrud exercitation ullamco laboris nisi ut aliquip ex ea commodo consequat. Duis aute irure dolor in reprehenderit in voluptate velit esse cillum dolore eu fugiat nulla pariatur. Excepteur sint occaecat cupidatat non proident, sunt in culpa qui officia deserunt mollit anim id est laborum.</p>
</section>

<article class="service" style="left:111px">
  <div class="service-icon"><svg width="70" height="50" viewBox="0 0 70 50"><path d="M6 8 L54 22 L50 34 L2 20 Z" fill="#111"/><rect x="52" y="22" width="6" height="14" fill="#111"/><rect x="46" y="34" width="20" height="5" fill="#111"/><path d="M20 26 L16 42 L6 42" stroke="#111" stroke-width="5" fill="none"/></svg></div>
  <h3>Fixed Camra Systems</h3>
  <p>Lorem ipsum dolor amet consectetur elit sed do eiusmod tempor incididunt ut labore et dolore magna aliqua.</p>
</article>
<article class="service" style="left:441px">
  <div class="service-icon"><svg width="66" height="60" viewBox="0 0 66 60"><g fill="none" stroke="#111" stroke-width="6"><circle cx="24" cy="24" r="13"/><circle cx="46" cy="42" r="9"/></g><g stroke="#111" stroke-width="6"><path d="M24 3v8M24 37v8M3 24h8M37 24h8M9 9l6 6M33 33l6 6M9 39l6-6M33 15l6-6"/><path d="M46 28v4M46 52v4M32 42h4M56 42h4"/></g></svg></div>
  <h3>Guard Services</h3>
  <p>Lorem ipsum dolor amet consectetur elit sed do eiusmod tempor incididunt ut labore et dolore magna aliqua.</p>
</article>
<article class="service" style="left:771px">
  <div class="service-icon"><svg width="66" height="60" viewBox="0 0 66 60"><path d="M6 6 L40 18 L38 36 L4 24 Z" fill="#111"/><rect x="30" y="24" width="26" height="20" rx="2" fill="none" stroke="#111" stroke-width="5"/><rect x="40" y="30" width="8" height="8" fill="#111"/><rect x="26" y="44" width="34" height="5" fill="#111"/></svg></div>
  <h3>Fixed Camra Systems</h3>
  <p>Lorem ipsum dolor amet consectetur elit sed do eiusmod tempor incididunt ut labore et dolore magna aliqua.</p>
</article>

<section class="plus">
  <span class="plus-dot"></span>
  <h2>SECURITY PLUS</h2>
  <p class="lead">Tempor incididunt ut labore et dolore magna aliqua ut enim!</p>
  <ul class="checklist">
    <li><svg width="14" height="12" viewBox="0 0 14 12"><path d="M1 6l4 4 8-9" stroke="#111" stroke-width="2.4" fill="none"/></svg>Lorem ipsum dolor amet consectetur elit sed do eiusmod</li>
    <li><svg width="14" height="12" viewBox="0 0 14 12"><path d="M1 6l4 4 8-9" stroke="#111" stroke-width="2.4" fill="none"/></svg>Tempor incididunt ut labore et dolore magna aliqua.</li>
    <li><svg width="14" height="12" viewBox="0 0 14 12"><path d="M1 6l4 4 8-9" stroke="#111" stroke-width="2.4" fill="none"/></svg>Ad minim veniam, quis nostrud exercitation ullamco laboris</li>
    <li><svg width="14" height="12" viewBox="0 0 14 12"><path d="M1 6l4 4 8-9" stroke="#111" stroke-width="2.4" fill="none"/></svg>Nisi ut aliquip ex ea commodo consequat.</li>
  </ul>
  <span class="btn-dark">READ MORE</span>
  <div class="plus-monitor" role="img" aria-label="Illustration of a desktop monitor showing a masked burglar taking a painting off a wall"></div>
</section>

<section class="why">
  <h2>WHY PEOPLE CHOOSE US?</h2>
  <p class="lead">Lorem ipsum dolor amet consectetur elit sed do eiusmod tempor incididunt ut labore et dolore. magna aliqua.</p>
  <article class="reason" style="left:111px">
    <div class="reason-photo" role="img" aria-label="Photo of a security control room with a wall of monitors" style="background:linear-gradient(135deg,#6f8fa8,#2d3b48)"></div>
    <h3>LOREM IPSUM DOLOR</h3>
    <p>Lorem ipsum dolor amet consectetur elit sed do eiusmod tempor incididunt ut labore et dolore magna aliqua.Ut enim ad minim veniam.</p>
  </article>
  <article class="reason" style="left:444px">
    <div class="reason-photo" role="img" aria-label="Photo of security cameras on a glass office building" style="background:linear-gradient(135deg,#3f7fb5,#a9c6dd)"></div>
    <h3>LOREM IPSUM DOLOR</h3>
    <p>Lorem ipsum dolor amet consectetur elit sed do eiusmod tempor incididunt ut labore et dolore magna aliqua.Ut enim ad minim veniam.</p>
  </article>
  <article class="reason" style="left:778px">
    <div class="reason-photo" role="img" aria-label="Photo of an access control keypad beside a glass door" style="background:linear-gradient(135deg,#8fae9e,#d9dcde)"></div>
    <h3>LOREM IPSUM DOLOR</h3>
    <p>Lorem ipsum dolor amet consectetur elit sed do eiusmod tempor incididunt ut labore et dolore magna aliqua.Ut enim ad minim veniam.</p>
  </article>
</section>

<section class="testimonials">
  <h2>Testimonials</h2>
  <p class="lead">Amet consectetur elit sed do eiusmod tempor incididunt ut labore et dolore magna aliqua.</p>
  <div class="avatar" role="img" aria-label="Portrait photo of the client" style="left:110px"></div>
  <blockquote class="quote-card" style="left:228px">
    <span class="mark open">“</span><span class="mark close">”</span>
    <p>Lorem ipsum dolor amet consectetur elit sed do eiusmod tempor incididunt ut labore et dolore magna aliqua.Ut enim ad minim veniam quis nostrud exercitation ullamco laboris nisi ut aliquip ex ea commodo consequat...</p>
    <cite>Owen Hartley</cite>
  </blockquote>
  <div class="avatar" role="img" aria-label="Portrait photo of the client" style="left:629px"></div>
  <blockquote class="quote-card" style="left:746px">
    <span class="mark open">“</span><span class="mark close">”</span>
    <p>Lorem ipsum dolor amet consectetur elit sed do eiusmod tempor incididunt ut labore et dolore magna aliqua.Ut enim ad minim veniam quis nostrud exercitation ullamco laboris nisi ut aliquip ex ea commodo consequat...</p>
    <cite>Lena Corvik</cite>
  </blockquote>
</section>

<footer class="site-footer">
  <div class="footer-col" style="left:142px">
    <h4>Site Map</h4>
    <ul><li class="active">Home</li><li>About Us</li><li>Security Services</li><li>Testimonials</li><li>Contct Us</li></ul>
  </div>
  <div class="footer-col" style="left:360px">
    <h4>Related links</h4>
    <ul><li>Lorem ipsum dolor</li><li>sit amet Consectetur</li><li>adipisicing elit Sed</li><li>do eiusmod tempor</li><li>incididunt ut labore</li></ul>
  </div>
  <div class="footer-col" style="left:607px">
    <h4>For Clients</h4>
    <ul><li>Sign Up</li><li>Forum</li><li>Policy</li></ul>
  </div>
  <div class="footer-col contact-col" style="left:821px">
    <h4><svg width="22" height="18" viewBox="0 0 22 18" style="margin-right:10px;vertical-align:-2px"><path d="M1 7 L11 1 L21 7 V17 H1 Z" fill="#aaa"/><path d="M1 7 L11 13 L21 7" stroke="#2b2b2b" stroke-width="1.6" fill="none"/></svg>Contact Information</h4>
    <div style="padding-left:34px">
      <p>Dolore magna aliqua ut enim ad laboris nisi ut aliquip</p>
      <p>E-mail: hello@tavronmail.co.nz</p>
      <p>Phone: +64 9 555 0142</p>
      <div class="social"><span></span><span></span><span></span><span></span><span></span></div>
    </div>
  </div>
  <div class="footer-rule"></div>
  <p class="copyright">Copy rigthe 2014 © Tavron. All rights reserved</p>
</footer>

</body>
</html>
```